Etikett für Rotweinflasche
Liebe farbkosmos Atelier, wir werden uns bei der endgültigen Etikettengestaltung (finale Größe + Rückseite) noch an Euch melden. Bitte sendet uns euren Kontakt an helga.brandt@morvelli.wine
Zielgruppe
Morvelli Italia ist ein exklusives Boutique-Weingut in Sizilien, das hochqualitative Spitzenweine in kleinen Mengen mit modernster Technologie und stets nachhaltig erzeugt. Wir hinterfragen sowohl in der Agronomie im Weingarten als auch in der Önologie im Weinkeller alle herrschenden Traditionen und trachten danach, stets das beste Endprodukt zu kreieren. Der vulkanische, kalkreiche Boden Siziliens sowie trockene, sonnenreiche und niederschlagsarme Vegetationsperioden sind unsere optimale Basis.
Zielgruppe: Internationale Genussmenschen jeglichen Alters, die sich bewusst auch höherpreisige Weine (um die €30+) gönnen , vor allem kunstaffine young professionals mit Qualitäts-& Nachhaltigkeitsanspruch
Aufgabenstellung
Das Etikett ist für Rotwein-Flaschen (Cabernet Sauvignon / Nero D'Avola / Frappato / Syrah / Cerasuolo / Petit Verdot / sowie einen Bourdeaux-Cuveè aus Cabernet Sauvignon und Petit Verdot) .
Die Flasche ist reinschwarz, sehr hochwertig und schwer.
Flaschenform: Bordeauxflasche siehe technisches Datenblatt
Sleeve über dem Korken: schwarz mit weißer Schrift wie bisher
Zu gestalten ist das Etikett der Vorderseite. Zumindest die jeweilige Rotwein-Sorte ist auch textlich darzustellen (zwecks Scannen mit Trubel-App)
Der Kreativität kann freien Lauf gelassen werden! Unterscheidbarkeit vom Markt ist explizit gewollt.
Unsere aktuellen Etiketten und Markenauftritt siehe: https://morvelli.wine/shop/

```html
<!DOCTYPE html>
<html lang="de">
<head>
<meta charset="utf-8">
<title>Etikett Cabernet Sauvignon</title>
<link rel="stylesheet" href="https://fonts.googleapis.com/css2?family=Playfair+Display+SC:wght@700&family=Roboto:wght@400&display=swap">
<style>
  :root {
    --page-bg: #ffffff;
    --label-plum: #2a1030;
    --label-wine: #6e1a22;
    --label-red: #a8301e;
    --label-orange: #e0782a;
    --label-gold: #f0c86a;
    --label-teal: #1f7f86;
    --label-navy: #14213a;
    --title-cream: #f4e4a4;
    --batch-white: #e8e4dc;
  }
  html, body {
    margin: 0;
    padding: 0;
    width: 849px;
    height: 1200px;
    overflow: hidden;
    background: var(--page-bg);
  }
  .canvas {
    position: relative;
    width: 849px;
    height: 1200px;
  }
  .front-label {
    position: absolute;
    left: 76px;
    top: 100px;
    width: 697px;
    height: 1000px;
    overflow: hidden;
    background: var(--label-plum);
  }
  .label-artwork {
    position: absolute;
    inset: 0;
    width: 100%;
    height: 100%;
    display: block;
  }
  .variety-name {
    position: absolute;
    top: 40px;
    left: 0;
    right: 0;
    margin: 0;
    text-align: center;
    font-family: "Playfair Display SC", serif;
    font-weight: 700;
    font-size: 38px;
    letter-spacing: 0.2em;
    color: var(--title-cream);
    transform: scaleX(0.78);
    transform-origin: center;
  }
  .batch-number {
    position: absolute;
    left: 10px;
    bottom: 14px;
    margin: 0;
    font-family: "Roboto", sans-serif;
    font-size: 15px;
    color: var(--batch-white);
    writing-mode: vertical-rl;
    transform: rotate(180deg);
  }
</style>
</head>
<body>
<main class="canvas">
  <section class="front-label">
    <svg class="label-artwork" viewBox="0 0 697 1000" role="img" aria-label="Illustration: zwei eng aneinander geschmiegte Figuren in facettierten Farbflächen aus Gold, Orange, Rot und Petrol vor dunkelrotem Grund">
      <defs>
        <radialGradient id="artwork-ground" cx="50%" cy="45%" r="70%">
          <stop offset="0" stop-color="var(--label-red)"/>
          <stop offset="0.55" stop-color="var(--label-wine)"/>
          <stop offset="1" stop-color="var(--label-plum)"/>
        </radialGradient>
        <radialGradient id="artwork-warm" cx="62%" cy="62%" r="45%">
          <stop offset="0" stop-color="var(--label-gold)" stop-opacity="0.85"/>
          <stop offset="0.5" stop-color="var(--label-orange)" stop-opacity="0.6"/>
          <stop offset="1" stop-color="var(--label-orange)" stop-opacity="0"/>
        </radialGradient>
        <radialGradient id="artwork-cool" cx="8%" cy="92%" r="35%">
          <stop offset="0" stop-color="var(--label-teal)" stop-opacity="0.85"/>
          <stop offset="1" stop-color="var(--label-teal)" stop-opacity="0"/>
        </radialGradient>
        <radialGradient id="artwork-dark" cx="45%" cy="28%" r="25%">
          <stop offset="0" stop-color="var(--label-navy)" stop-opacity="0.7"/>
          <stop offset="1" stop-color="var(--label-navy)" stop-opacity="0"/>
        </radialGradient>
      </defs>
      <rect width="697" height="1000" fill="url(#artwork-ground)"/>
      <rect width="697" height="1000" fill="url(#artwork-warm)"/>
      <rect width="697" height="1000" fill="url(#artwork-cool)"/>
      <rect width="697" height="1000" fill="url(#artwork-dark)"/>
    </svg>
    <h1 class="variety-name">Cabernet Sauvignon</h1>
    <p class="batch-number">029</p>
  </section>
</main>
</body>
</html>
```